Residential Remodeling Contractor needs updated business card

I need a new design for my business card.
Name of the company is Ridgefell Construction. I need a card that commands presence, strength, integrity. I have been in business for 28 years. I am a Residential Remodeling Contractor that covers all aspects of a residential remodel and build.

```html
<!DOCTYPE html>
<html lang="en">
<head>
<meta charset="utf-8">
<title>Ridgefell Construction — Business Card</title>
<link rel="stylesheet" href="https://fonts.googleapis.com/css2?family=Open+Sans:wght@400;600;700&display=swap">
<style>
  :root {
    --stage: #232323;
    --card-blue: #213e7e;
    --card-deep: #1a3268;
    --emboss: #2c4f9c;
    --paper: #ffffff;
    --shadow: rgba(0, 0, 0, 0.45);
  }
  * { box-sizing: border-box; margin: 0; padding: 0; }
  html, body {
    width: 1200px;
    height: 780px;
    overflow: hidden;
    background: var(--stage);
    font-family: "Open Sans", Arial, sans-serif;
  }
  .canvas {
    width: 1200px;
    height: 780px;
    display: flex;
    align-items: center;
    justify-content: center;
    gap: 40px;
  }
  .card {
    position: relative;
    width: 540px;
    height: 309px;
    background: var(--card-blue);
    box-shadow: 0 18px 40px var(--shadow);
    overflow: hidden;
    color: var(--paper);
  }

  /* Front: contact side */
  .brand {
    position: absolute;
    left: 120px;
    top: 26px;
    font-weight: 600;
    font-size: 24px;
    line-height: 1.12;
    letter-spacing: 0.06em;
    text-transform: uppercase;
    color: var(--paper);
  }
  .brand-mark {
    position: absolute;
    left: 86px;
    top: 34px;
    width: 22px;
    height: 22px;
    background: var(--paper);
  }
  .contact {
    position: absolute;
    left: 28px;
    top: 118px;
    font-size: 12px;
    line-height: 1.55;
    list-style: none;
  }
  .contact li { display: flex; align-items: center; gap: 6px; }
  .contact .address { padding-left: 20px; }
  .contact svg { width: 14px; height: 14px; flex: none; }
  .rule {
    position: absolute;
    left: 150px;
    top: 262px;
    width: 195px;
    height: 1.5px;
    background: var(--paper);
  }
  .person {
    position: absolute;
    right: 34px;
    top: 222px;
    text-align: left;
  }
  .person-name {
    font-weight: 700;
    font-size: 30px;
    line-height: 1;
    letter-spacing: 0.01em;
  }
  .person-title {
    margin-top: 6px;
    margin-left: 8px;
    font-size: 14px;
    font-weight: 400;
  }
  .edge-block {
    position: absolute;
    right: 0;
    top: 238px;
    width: 22px;
    height: 50px;
    background: var(--paper);
  }

  /* Back: name side */
  .card-back {
    display: flex;
    align-items: center;
    justify-content: center;
    background: linear-gradient(160deg, var(--card-blue), var(--card-deep));
  }
  .back-brand {
    font-weight: 600;
    font-size: 38px;
    line-height: 1.1;
    letter-spacing: 0.07em;
    text-transform: uppercase;
    text-align: center;
    color: var(--emboss);
  }
</style>
</head>
<body>
<main class="canvas">
  <section class="card card-front" aria-label="Business card, contact side">
    <span class="brand-mark"></span>
    <h1 class="brand">Ridgefell<br>Construction</h1>

    <ul class="contact">
      <li class="address">4180 Cedar Hollow Rd. Suite 210</li>
      <li class="address">Amberton, TX 75409</li>
      <li>
        <svg viewBox="0 0 16 16" aria-hidden="true"><path d="M4 1.5l2.2 2.6-1.3 1.6c.8 2 2.4 3.6 4.4 4.4l1.6-1.3 2.6 2.2-1.4 2.3C7 13 3 9 1.7 2.9z" fill="#fff"/></svg>
        (555) 214-3086
      </li>
      <li>
        <svg viewBox="0 0 16 16" aria-hidden="true"><rect x="1.5" y="3.5" width="13" height="9" fill="none" stroke="#fff" stroke-width="1.4"/><path d="M1.5 3.5l6.5 5 6.5-5" fill="none" stroke="#fff" stroke-width="1.4"/></svg>
        info@ridgefellbuild.com
      </li>
      <li>
        <svg viewBox="0 0 16 16" aria-hidden="true"><circle cx="8" cy="8" r="6.3" fill="none" stroke="#fff" stroke-width="1.3"/><ellipse cx="8" cy="8" rx="2.7" ry="6.3" fill="none" stroke="#fff" stroke-width="1.1"/><path d="M1.7 8h12.6" stroke="#fff" stroke-width="1.1"/></svg>
        www.ridgefellbuild.com
      </li>
    </ul>

    <span class="rule"></span>
    <div class="person">
      <p class="person-name">Mara Velkova</p>
      <p class="person-title">Managing Director</p>
    </div>
    <span class="edge-block"></span>
  </section>

  <section class="card card-back" aria-label="Business card, name side">
    <p class="back-brand">Ridgefell<br>Construction</p>
  </section>
</main>
</body>
</html>
```